BRISKLY sparkling water needs new artwork! Based in Southern California

"Briskly" is a new sparkling water company based in Southern California that offers refreshing flavors (lime, cherry, & mango) with B vitamins and antioxidants.

We would like to see packaging designs for standard 12oz cans for each of the three flavors.
Our initial preference is to have individual artwork for each flavor.

Attached are examples of competitors' designs.
Updates

We are extending the deadline for the Thanksgiving Holiday. Thank you all for your contributions.

```html
<!DOCTYPE html>
<html lang="en">
<head>
<meta charset="utf-8">
<title>Briskly Sparkling Water – 12oz Can Label Templates</title>
<link rel="stylesheet" href="https://fonts.googleapis.com/css2?family=Montserrat:wght@400;500;600;700;800&family=Source+Sans+3:wght@400;600;700&display=swap">
<style>
  :root {
    --guide: #9b87c4;
    --guide-text: #8f7bbd;
    --ink: #1d1d1b;
    --white: #ffffff;
    --page: #ffffff;
  }
  html, body {
    margin: 0;
    padding: 0;
    width: 1200px;
    height: 2297px;
    overflow: hidden;
    background: var(--page);
  }
  .sheet { display: block; width: 1200px; height: 2297px; }

  .flavor-cherry { --bg: #fdf0f2; --accent: #e0105a; --logo: #e0105a; --fruit: #e8323a;
    --w1: #f4a9b6; --w2: #e95b74; --w3: #e0105a; --w4: #a8063a; --w5: #e0105a; }
  .flavor-mango { --bg: #fafbe3; --accent: #f39a1d; --logo: #f5a623; --fruit: #fbc02d;
    --w1: #fde74c; --w2: #f9bf1e; --w3: #fdd835; --w4: #fbc02d; --w5: #ffeb55; }
  .flavor-lime { --bg: #f5fae4; --accent: #5ba82a; --logo: #3cb52a; --fruit: #b5dd5a;
    --w1: #6b9e1a; --w2: #7db81c; --w3: #5f8f16; --w4: #86c21f; --w5: #78b51a; }

  .template-title { font: 400 28px "Source Sans 3", sans-serif; fill: var(--guide-text); text-anchor: middle; }
  .guide-note { font: 400 12px "Source Sans 3", sans-serif; fill: var(--guide-text); }
  .guide-note-sm { font: 400 9px "Source Sans 3", sans-serif; fill: var(--guide-text); }
  .guide-strong { font: 700 13px "Source Sans 3", sans-serif; fill: var(--guide-text); }
  .guide-dim { font: 400 12px "Source Sans 3", sans-serif; fill: var(--guide-text); text-anchor: middle; }
  .center { text-anchor: middle; }
  .end { text-anchor: end; }

  .guide-line { stroke: var(--guide); stroke-width: 1; fill: none; }
  .guide-dash { stroke: var(--guide); stroke-width: 1.2; stroke-dasharray: 8 5; fill: none; }
  .guide-dot { stroke: var(--guide); stroke-width: 0.8; stroke-dasharray: 3 3; fill: none; }

  .label-bg { fill: var(--bg); }
  .fruit-zone { fill: var(--fruit); opacity: 0.16; }
  .wave-1 { fill: var(--w1); } .wave-2 { fill: var(--w2); } .wave-3 { fill: var(--w3); }
  .wave-4 { fill: var(--w4); } .wave-5 { fill: var(--w5); }

  .brand-name { font: 700 58px "Montserrat", sans-serif; fill: var(--logo); text-anchor: middle; }
  .product-type { font: 600 25px "Montserrat", sans-serif; fill: var(--ink); text-anchor: middle; letter-spacing: 1px; }
  .product-rule { stroke: var(--accent); stroke-width: 2.5; }
  .claims { font: 400 11px "Montserrat", sans-serif; fill: var(--ink); text-anchor: middle; }
  .flavor-pill { fill: var(--accent); }
  .flavor-name { font: 700 12px "Montserrat", sans-serif; fill: var(--white); text-anchor: middle; letter-spacing: 3px; }
  .volume { font: 600 19px "Montserrat", sans-serif; fill: var(--white); text-anchor: middle; }

  .claim-badge { fill: var(--white); stroke: var(--accent); stroke-width: 1.6; }
  .claim-seal { fill: var(--accent); }
  .claim-num { font: 700 10px "Montserrat", sans-serif; fill: var(--accent); text-anchor: middle; }
  .claim-word { font: 600 3.6px "Montserrat", sans-serif; fill: var(--accent); text-anchor: middle; }

  .info-box { fill: var(--white); stroke: var(--ink); stroke-width: 0.8; }
  .info-label { font: 700 7px "Montserrat", sans-serif; fill: var(--ink); }
  .boost-ring { fill: var(--white); stroke: var(--accent); stroke-width: 3; }
  .boost-text { font: 700 12px "Montserrat", sans-serif; fill: var(--accent); text-anchor: middle; }
  .boost-arc { fill: none; stroke: var(--accent); stroke-width: 2; }
</style>
</head>
<body>
<svg class="sheet" viewBox="0 0 1350 2584" preserveAspectRatio="none" xmlns="http://www.w3.org/2000/svg" xmlns:xlink="http://www.w3.org/1999/xlink">
  <defs>
    <clipPath id="label-clip" clipPathUnits="userSpaceOnUse">
      <rect x="204" y="245" width="926" height="508"/>
      <rect x="443" y="245" width="448" height="522"/>
    </clipPath>
    <path id="wave-band" d="M190 12 C260 -6 330 22 410 8 S560 -10 640 10 S780 26 860 6 S1000 -8 1070 12 S1130 4 1150 8 V240 H190 Z"/>
    <marker id="dim-arrow" markerWidth="8" markerHeight="8" refX="7" refY="4" orient="auto-start-reverse">
      <path d="M0 1 L7 4 L0 7" fill="none" stroke="#9b87c4" stroke-width="1"/>
    </marker>

    <g id="template-guides">
      <text class="template-title" x="683" y="128">109 mm LF_4.875″_Template</text>
      <text class="guide-note" x="182" y="170">1 mm clear</text>
      <text class="guide-note end" x="1146" y="170">5 mm clear</text>
      <text class="guide-strong" x="1156" y="172">Transitional Area</text>
      <text class="guide-note-sm" x="1156" y="185">(transitions from sidewall to neck)</text>
      <line class="guide-line" x1="1167" y1="193" x2="1122" y2="247" marker-end="url(#dim-arrow)"/>
      <circle cx="1167" cy="193" r="2.5" fill="#9b87c4"/>
      <text class="guide-note center" x="678" y="190">109 mm LF</text>

      <line class="guide-line" x1="209" y1="200" x2="209" y2="245"/>
      <line class="guide-line" x1="213" y1="200" x2="213" y2="245"/>
      <line class="guide-line" x1="1108" y1="190" x2="1108" y2="245"/>
      <line class="guide-dot" x1="1105" y1="230" x2="1105" y2="780"/>
      <line class="guide-dot" x1="209" y1="753" x2="209" y2="800"/>
      <line class="guide-line" x1="1129" y1="760" x2="1129" y2="808"/>

      <text class="guide-note" x="52" y="255">2 mm clear</text>
      <line class="guide-line" x1="125" y1="246" x2="175" y2="246"/>
      <line class="guide-line" x1="125" y1="252" x2="175" y2="252"/>
      <text class="guide-note" x="1205" y="255">2 mm clear</text>
      <line class="guide-line" x1="1147" y1="246" x2="1197" y2="246"/>
      <line class="guide-line" x1="1147" y1="252" x2="1197" y2="252"/>
      <text class="guide-note" x="54" y="753">2 mm clear</text>
      <line class="guide-line" x1="127" y1="745" x2="177" y2="745"/>
      <line class="guide-line" x1="127" y1="751" x2="177" y2="751"/>
      <text class="guide-note" x="1210" y="753">2 mm clear</text>
      <line class="guide-line" x1="1152" y1="745" x2="1202" y2="745"/>
      <line class="guide-line" x1="1152" y1="751" x2="1202" y2="751"/>

      <text class="guide-note" x="1151" y="481">4.875″ Cut Height</text>
      <text class="guide-note" x="1151" y="498">123.825 MM</text>

      <line class="guide-line" x1="212" y1="784" x2="588" y2="784" marker-start="url(#dim-arrow)"/>
      <line class="guide-line" x1="731" y1="784" x2="1126" y2="784" marker-end="url(#dim-arrow)"/>
      <text class="guide-dim" x="657" y="788">225 MM SLIT WIDTH</text>
      <text class="guide-dim" x="657" y="804">8.8583″</text>
      <text class="guide-note-sm center" x="1045" y="811">2mm Bkgd Only</text>
      <text class="guide-note-sm center" x="1045" y="824">No Text/Art</text>
      <text class="guide-note-sm center" x="240" y="830">1mm Bkgd Bleed</text>
      <text class="guide-note-sm center" x="240" y="843">Overlap</text>
    </g>

    <g id="label-copy">
      <text class="brand-name" x="659" y="401">Briskly</text>
      <text class="product-type" x="659" y="456">SPARKLING</text>
      <text class="product-type" x="659" y="483">WATER</text>
      <line class="product-rule" x1="617" y1="495" x2="701" y2="495"/>
      <text class="claims" x="659" y="518">NATURAL FLAVORS</text>
      <text class="claims" x="659" y="534">&amp; B-VITAMINS</text>
    </g>

    <g id="claim-column">
      <circle class="claim-badge" cx="389" cy="349" r="13"/>
      <text class="claim-num" x="389" y="350">0</text><text class="claim-word" x="389" y="356">SUGAR</text>
      <circle class="claim-badge" cx="389" cy="385" r="13"/>
      <text class="claim-num" x="389" y="386">0</text><text class="claim-word" x="389" y="392">CALORIES</text>
      <circle class="claim-badge" cx="389" cy="422" r="13"/>
      <text class="claim-num" x="389" y="423">0</text><text class="claim-word" x="389" y="429">SODIUM</text>
      <circle class="claim-badge" cx="389" cy="460" r="13"/>
      <text class="claim-word" x="389" y="459" style="font-size:5px">B6 &amp;</text><text class="claim-word" x="389" y="465" style="font-size:5px">B12</text>
      <circle class="claim-badge" cx="389" cy="498" r="13"/>
      <circle class="claim-badge" cx="389" cy="536" r="13"/>
      <circle class="claim-seal" cx="389" cy="536" r="7"/>
      <circle class="claim-badge" cx="389" cy="575" r="13"/>
      <circle class="claim-seal" cx="389" cy="575" r="7"/>
    </g>

    <g id="back-panel">
      <rect class="info-box" x="907" y="351" width="124" height="172"/>
      <text class="info-label" x="932" y="367">NUTRITION PANEL</text>
      <rect class="info-box" x="1040" y="441" width="56" height="82"/>
      <text class="info-label" transform="translate(1070 500) rotate(-90)">BARCODE</text>
    </g>
  </defs>

  <!-- Cherry -->
  <g class="flavor-cherry">
    <rect class="label-bg" x="204" y="245" width="926" height="508"/>
    <g clip-path="url(#label-clip)">
      <rect class="fruit-zone" x="204" y="245" width="926" height="370" role="img" aria-label="Scattered cherry illustrations with leaves across the label"/>
      <use href="#wave-band" class="wave-1" y="598"/>
      <use href="#wave-band" class="wave-2" y="628"/>
      <use href="#wave-band" class="wave-3" y="656"/>
      <use href="#wave-band" class="wave-4" y="686"/>
      <use href="#wave-band" class="wave-5" y="716"/>
    </g>
    <use href="#label-copy"/>
    <rect class="flavor-pill" x="614" y="545" width="90" height="19" rx="9.5"/>
    <text class="flavor-name" x="660" y="559">CHERRY</text>
    <text class="volume" x="659" y="732">12oz</text>
    <use href="#claim-column"/>
    <use href="#back-panel"/>
    <circle class="boost-ring" cx="997" cy="572" r="36"/>
    <text class="boost-text" x="997" y="568">BOOST</text>
    <text class="boost-text" x="997" y="584">IMMUNITY</text>
    <path class="boost-arc" d="M975 592 Q997 606 1019 592"/>
    <rect x="204" y="245" width="926" height="508" class="guide-line"/>
    <rect x="209" y="253" width="899" height="492" class="guide-line" stroke-width="0.6"/>
    <rect x="443" y="203" width="448" height="564" class="guide-line"/>
    <line class="guide-dash" x1="178" y1="303" x2="1157" y2="303"/>
    <use href="#template-guides"/>
  </g>

  <!-- Mango -->
  <g class="flavor-mango" transform="translate(0 886)">
    <rect class="label-bg" x="204" y="245" width="926" height="508"/>
    <g clip-path="url(#label-clip)">
      <rect class="fruit-zone" x="204" y="245" width="926" height="360" role="img" aria-label="Scattered mango halves, whole mangoes and leaves across the label"/>
      <use href="#wave-band" class="wave-1" y="598"/>
      <use href="#wave-band" class="wave-2" y="620"/>
      <use href="#wave-band" class="wave-3" y="650"/>
      <use href="#wave-band" class="wave-4" y="680"/>
      <use href="#wave-band" class="wave-5" y="708"/>
    </g>
    <use href="#label-copy"/>
    <rect class="flavor-pill" x="617" y="545" width="84" height="19" rx="9.5"/>
    <text class="flavor-name" x="660" y="559">MANGO</text>
    <text class="volume" x="659" y="732" style="fill:#8a5a00">12oz</text>
    <g transform="translate(9 0)"><use href="#claim-column"/></g>
    <use href="#back-panel"/>
    <circle class="boost-ring" cx="1003" cy="567" r="32"/>
    <text class="boost-text" x="1003" y="563">BOOST</text>
    <text class="boost-text" x="1003" y="578">IMMUNITY</text>
    <path class="boost-arc" d="M983 586 Q1003 598 1023 586"/>
    <rect x="204" y="245" width="926" height="508" class="guide-line"/>
    <rect x="209" y="253" width="899" height="492" class="guide-line" stroke-width="0.6"/>
    <rect x="443" y="203" width="448" height="564" class="guide-line"/>
    <line class="guide-dash" x1="178" y1="303" x2="1157" y2="303"/>
    <use href="#template-guides"/>
  </g>

  <!-- Lime -->
  <g class="flavor-lime" transform="translate(0 1731)">
    <rect class="label-bg" x="204" y="245" width="926" height="508"/>
    <g clip-path="url(#label-clip)">
      <rect class="fruit-zone" x="204" y="245" width="926" height="390" role="img" aria-label="Scattered lime slices of various sizes across the label"/>
      <use href="#wave-band" class="wave-1" y="626"/>
      <use href="#wave-band" class="wave-2" y="652"/>
      <use href="#wave-band" class="wave-3" y="676"/>
      <use href="#wave-band" class="wave-4" y="700"/>
      <use href="#wave-band" class="wave-5" y="724"/>
    </g>
    <use href="#label-copy"/>
    <rect class="flavor-pill" x="622" y="545" width="74" height="19" rx="9.5"/>
    <text class="flavor-name" x="660" y="559">LIME</text>
    <text class="volume" x="659" y="732">12oz</text>
    <g transform="translate(10 0)"><use href="#claim-column"/></g>
    <use href="#back-panel"/>
    <circle class="boost-ring" cx="999" cy="567" r="33"/>
    <text class="boost-text" x="999" y="563">BOOST</text>
    <text class="boost-text" x="999" y="578">IMMUNITY</text>
    <path class="boost-arc" d="M979 587 Q999 599 1019 587"/>
    <rect x="204" y="245" width="926" height="508" class="guide-line"/>
    <rect x="209" y="253" width="899" height="492" class="guide-line" stroke-width="0.6"/>
    <rect x="443" y="203" width="448" height="564" class="guide-line"/>
    <line class="guide-dash" x1="178" y1="303" x2="1157" y2="303"/>
    <use href="#template-guides"/>
  </g>
</svg>
</body>
</html>
```